Velk Partners Building Business Cards

We need a business card that reflects our business as "Solar Experts" in San Diego. Browse our website www.velkpartners.example our License needs to be displayed as "CSLB# 3867140" our phone number is (619) 555-0187

Save thousands on your electric bills and increase the value of your home while helping to protect the environment. Our solar installation experts will help you design the system that's right for you, using only the highest quality equipment that will look great and give you ideal performance. Our goal is to make you energy independent, and get your electric bill to 0.

Paul Osterby
(619) 555-0187
paul@velkpartners.example

Target Market(s)

Home owners in san diego looking for solar

Industry/Entity Type

Solar Energy

Contact Information for Business Card

Paul Osterby
(619) 555-0187
paul@velkpartners.example

Font styles to use
Other font styles liked:
• Use our logo font

Requirements
Must have
• License needs to be displayed as "CSLB# 3867140" our phone number is (619) 555-0187
Nice to have
• Real images of rooftop home solar in san diego
Should not have
• our business address

```html
<!DOCTYPE html>
<html lang="en">
<head>
<meta charset="utf-8">
<title>Velk Partners Building – Business Card</title>
<link href="https://fonts.googleapis.com/css2?family=Roboto:wght@400;500;700&display=swap" rel="stylesheet">
<style>
  :root {
    --navy: #1f3c6e;
    --gold: #e0900f;
    --ink: #2b3340;
    --card: #eef0f1;
    --card-edge: #d3d7da;
    --backdrop: #dcd8d2;
  }
  * { margin: 0; padding: 0; box-sizing: border-box; }
  html, body {
    width: 1200px; height: 1200px; overflow: hidden;
    background: var(--backdrop);
    font-family: "Roboto", Arial, sans-serif;
  }
  .stage {
    width: 1200px; height: 1200px;
    display: flex; align-items: center; justify-content: center;
  }
  .business-card {
    position: relative;
    width: 1000px; height: 592px;
    background: var(--card);
    border: 1px solid var(--card-edge);
    box-shadow: 0 10px 30px rgba(0,0,0,0.12);
    overflow: hidden;
  }
  .side-band {
    position: absolute; left: 0; top: 0; bottom: 0;
    width: 87px; background: var(--navy);
  }
  .side-stripe {
    position: absolute; left: 87px; top: 0; bottom: 0;
    width: 9px; background: var(--gold);
  }
  .company-name {
    position: absolute; right: 66px; top: 40px;
    text-align: right;
    color: var(--navy);
    font-weight: 700;
    font-size: 54px; line-height: 1.05;
    letter-spacing: -0.5px;
  }
  .company-name .line-two { display: block; font-size: 34px; letter-spacing: 3px; }
  .person-name {
    position: absolute; left: 139px; top: 278px;
    color: var(--navy); font-weight: 700; font-size: 33px;
  }
  .person-title {
    position: absolute; left: 139px; top: 324px;
    color: var(--ink); font-size: 22px;
  }
  .contact-list {
    position: absolute; left: 139px; top: 398px;
    list-style: none;
  }
  .contact-list li {
    display: flex; align-items: center;
    height: 35px;
    color: var(--ink); font-size: 25px;
  }
  .contact-list svg { width: 26px; height: 22px; margin-right: 24px; fill: var(--gold); }
  .contact-list .accent { color: var(--gold); }
  .license {
    position: absolute; left: 139px; top: 514px;
    color: var(--ink); font-size: 24px;
  }
</style>
</head>
<body>
<div class="stage">
  <div class="business-card">
    <div class="side-band"></div>
    <div class="side-stripe"></div>

    <div class="company-name">Velk Partners<span class="line-two">BUILDING</span></div>

    <div class="person-name">Paul Osterby</div>
    <div class="person-title">Managing Director</div>

    <ul class="contact-list">
      <li>
        <svg viewBox="0 0 26 22" aria-hidden="true">
          <path d="M3 5c0-2 3-3 10-3s10 1 10 3v3h-5V6H8v2H3z"/>
          <rect x="5" y="10" width="16" height="11" rx="2"/>
        </svg>
        (619) 555-0187
      </li>
      <li>
        <svg viewBox="0 0 26 22" aria-hidden="true">
          <circle cx="13" cy="11" r="10"/>
          <path d="M3 11h20M13 1v20" stroke="#eef0f1" stroke-width="1.6" fill="none"/>
          <ellipse cx="13" cy="11" rx="4.5" ry="10" stroke="#eef0f1" stroke-width="1.6" fill="none"/>
        </svg>
        paul@velkpartners.example
      </li>
      <li>
        <svg viewBox="0 0 26 22" aria-hidden="true">
          <rect x="1" y="3" width="24" height="16"/>
          <path d="M1 3l12 9 12-9" stroke="#eef0f1" stroke-width="1.8" fill="none"/>
        </svg>
        www.<span class="accent">velkpartners</span>.example
      </li>
    </ul>

    <div class="license">License: CSLB# 3867140</div>
  </div>
</div>
</body>
</html>
```